KVM Contracting services . Building and maintenance services, optic fibre installation

Business cards and logo design.I need a logo that I can use on business cards ,workwear and on my vehicles. I would like the KVM to be the main or larger text and contracting services to be the smaller or less important text.I like monograms, modern designs and repeating patterns symbols. I am also a Gemini and my favourite number is 22 so if this can be any inspiration to help with the design. Am thinking of the using German flag colours as a his is my family’s heritage. And the other 2 main colours I wear is black and white.But any ideas are appreciated.I do not need a design that is trade specific but a design that could be used for any business.

Target Market(s)

General public

Contact Information for Business Card

KVM Contracting Services ( front of business card)

(Back of business card)
Darren Holtwick
0451907326
Maintenance services
Optic fibre and data installation

Logo Text

Logo can just be pattern or monogram or incorporate KVM . I like the gemini star sign and the number 22

Colors
ec1f27
000000
fbee3e
ffffff

Requirements
Must have
• Logo and KVM Contracting Services on the front of business card
Nice to have
• Possible use of German flag colours.
• Modern design.
• Design to be able to be used on black or white background as I want to put it on clothing

```html
<!DOCTYPE html>
<html lang="en">
<head>
<meta charset="utf-8">
<title>KVM Contracting Services – Business Cards</title>
<link href="https://fonts.googleapis.com/css2?family=Montserrat:wght@500;800;900&family=Lato:wght@400;700&display=swap" rel="stylesheet">
<style>
  :root {
    --red: #e0202a;
    --yellow: #f7c81c;
    --black: #0a0a0a;
    --white: #ffffff;
    --ink: #1b1b1b;
    --backdrop: #2b2b2b;
  }
  * { box-sizing: border-box; margin: 0; padding: 0; }
  html, body { width: 1200px; height: 930px; overflow: hidden; }
  body {
    background: var(--backdrop);
    font-family: "Lato", sans-serif;
    position: relative;
  }
  .card {
    position: absolute;
    left: 290px;
    width: 620px;
    height: 354px;
    border-radius: 18px;
    overflow: hidden;
    box-shadow: 0 14px 30px rgba(0,0,0,.45);
  }
  .card--back { top: 80px; background: var(--black); }
  .card--front { top: 496px; background: var(--white); }

  .brand {
    font-family: "Montserrat", sans-serif;
    font-weight: 900;
    color: var(--red);
    line-height: 1;
    display: flex;
    align-items: center;
    gap: 14px;
  }
  .brand__mark {
    width: 22px; height: 22px;
    background: var(--yellow);
    flex: none;
  }
  .brand__name { display: flex; flex-direction: column; }
  .brand__initials { font-size: 92px; letter-spacing: 2px; }
  .brand__tagline { font-size: 20px; letter-spacing: .5px; text-transform: uppercase; margin-top: 4px; }

  .card--back .brand { position: absolute; left: 160px; top: 70px; }
  .services {
    position: absolute;
    left: 0; right: 0; top: 238px;
    text-align: center;
    font-family: "Montserrat", sans-serif;
    font-weight: 500;
    font-size: 15px;
    letter-spacing: 1px;
    text-transform: uppercase;
    line-height: 1.5;
  }
  .services__primary { color: var(--yellow); }
  .services__secondary { color: var(--white); }

  .card--front .brand { position: absolute; left: 46px; top: 110px; }
  .card--front .brand__initials { font-size: 80px; }
  .card--front .brand__tagline { font-size: 17px; }

  .divider {
    position: absolute;
    left: 320px; top: 66px;
    width: 2px; height: 180px;
    background: var(--ink);
  }
  .contact {
    position: absolute;
    left: 346px; top: 62px;
    color: var(--ink);
    font-size: 15px;
    line-height: 1.45;
  }
  .contact__name {
    font-family: "Montserrat", sans-serif;
    font-weight: 500;
    font-size: 23px;
    color: var(--red);
    text-transform: uppercase;
    line-height: 1.1;
  }
  .contact__role { font-size: 15px; margin-bottom: 12px; }
  .contact__address { margin-bottom: 8px; }
  .contact__line { display: flex; align-items: center; gap: 8px; }
  .contact__line svg { width: 12px; height: 12px; flex: none; }

  .stripe { position: absolute; left: 0; bottom: 0; width: 620px; height: 60px; }
</style>
</head>
<body>

<section class="card card--back" aria-label="Business card back">
  <div class="brand">
    <span class="brand__mark"></span>
    <span class="brand__name">
      <span class="brand__initials">KVM</span>
      <span class="brand__tagline">Contracting Services</span>
    </span>
  </div>
  <div class="services">
    <div class="services__primary">Maintenance Services</div>
    <div class="services__secondary">Optic Fibre and Data Installation</div>
  </div>
</section>

<section class="card card--front" aria-label="Business card front">
  <div class="brand">
    <span class="brand__mark"></span>
    <span class="brand__name">
      <span class="brand__initials">KVM</span>
      <span class="brand__tagline">Contracting Services</span>
    </span>
  </div>

  <div class="divider"></div>

  <div class="contact">
    <div class="contact__name">Darren Holtwick</div>
    <div class="contact__role">Director</div>
    <div class="contact__address">17 Larchmont Rd,<br>Milbrook, FL 32990, USA</div>
    <div class="contact__line">
      <svg viewBox="0 0 12 12" aria-hidden="true"><path d="M2.5 1 L4.5 1 L5.2 3.6 L4 4.6 Q5 6.9 7.4 8 L8.4 6.8 L11 7.5 L11 9.5 Q10.6 11 9 11 Q1 10 1 2.8 Q1 1 2.5 1 Z" fill="var(--red)"/></svg>
      <span>0451907326</span>
    </div>
    <div class="contact__line">
      <svg viewBox="0 0 12 12" aria-hidden="true"><rect x="1" y="2.5" width="10" height="7" fill="none" stroke="var(--red)" stroke-width="1.3"/><path d="M1 2.5 L6 6.5 L11 2.5" fill="none" stroke="var(--red)" stroke-width="1.3"/></svg>
      <span>office@kvmcontractingco.com</span>
    </div>
    <div class="contact__line">
      <svg viewBox="0 0 12 12" aria-hidden="true"><circle cx="6" cy="6" r="5" fill="none" stroke="var(--red)" stroke-width="1.2"/><ellipse cx="6" cy="6" rx="2.2" ry="5" fill="none" stroke="var(--red)" stroke-width="1"/><path d="M1 6 H11" stroke="var(--red)" stroke-width="1"/></svg>
      <span>www.kvmcontractingco.com</span>
    </div>
  </div>

  <svg class="stripe" viewBox="0 0 620 60" preserveAspectRatio="none" aria-hidden="true">
    <polygon points="0,46 352,46 372,14 620,14 620,24 382,24 362,60 0,60" fill="var(--yellow)"/>
    <polygon points="0,46 352,46 362,30 362,60 0,60" fill="var(--red)"/>
    <polygon points="0,48 350,48 372,14 380,14 356,60 0,60" fill="var(--red)"/>
  </svg>
</section>

</body>
</html>
```